Business Card Design (NEW FILES)

ATTENTION: New vector files are available. Please update your design to reflect/use the new (better resolution) logo images.

Seeking a unique and professional business card design for a commercial drone photography/videography business. The layout should feature
the logo (attached) and include the following information:
Owen Tarrick
614-502-7738
www.skylarkreelworks.example
NRD Certified Remote Pilot

Owen Tarrick

```html
<!DOCTYPE html>
<html lang="en">
<head>
<meta charset="utf-8">
<title>Skylark Reelworks – Business Card</title>
<link href="https://fonts.googleapis.com/css2?family=Open+Sans:wght@400;600;700&display=swap" rel="stylesheet">
<style>
  :root {
    --backdrop: #d9cdb9;
    --card: #ece3d3;
    --card-edge: #f4eee4;
    --orange: #d9712f;
    --navy: #1b1f3f;
  }
  * { margin: 0; padding: 0; box-sizing: border-box; }
  html, body {
    width: 1200px; height: 1046px; overflow: hidden;
    background: var(--backdrop);
    font-family: "Open Sans", sans-serif;
    color: var(--navy);
  }
  .card {
    position: absolute; left: 100px; top: 250px;
    width: 1000px; height: 545px;
    background: var(--card);
    border: 1px solid var(--card-edge);
    border-radius: 34px;
  }
  .accent-bar {
    position: absolute; top: 136px; width: 13px; height: 273px;
    background: var(--orange);
  }
  .accent-bar--left { left: 2px; }
  .accent-bar--right { right: 2px; }
  .divider {
    position: absolute; left: 503px; top: 160px;
    width: 2px; height: 225px; background: var(--orange);
  }
  .brand {
    position: absolute; left: 48px; top: 205px;
    display: flex; align-items: center; gap: 16px;
  }
  .brand__name {
    font-weight: 600; font-size: 40px; line-height: 1.05;
    color: var(--navy); letter-spacing: 1px;
  }
  .brand__dot {
    width: 42px; height: 42px; border-radius: 50%;
    background: var(--orange); flex: none;
  }
  .contact {
    position: absolute; left: 598px; top: 183px;
  }
  .contact__name {
    font-weight: 700; font-size: 40px; line-height: 1;
  }
  .contact__name .first { color: var(--orange); }
  .contact__role {
    font-weight: 600; font-size: 22px; margin-top: 8px; margin-left: 2px;
  }
  .contact__list { list-style: none; margin-top: 30px; }
  .contact__item {
    display: flex; align-items: center; gap: 16px;
    font-weight: 600; font-size: 22px; height: 33px;
  }
  .contact__item svg { width: 20px; height: 20px; flex: none; }
  .credentials {
    position: absolute; left: 0; right: 0; top: 444px;
    text-align: center; font-weight: 600; font-size: 22px; line-height: 32px;
  }
</style>
</head>
<body>
  <section class="card">
    <div class="accent-bar accent-bar--left"></div>
    <div class="accent-bar accent-bar--right"></div>

    <div class="brand">
      <div class="brand__name">SKYLARK<br>REELWORKS</div>
      <div class="brand__dot"></div>
    </div>

    <div class="divider"></div>

    <div class="contact">
      <div class="contact__name"><span class="first">Owen</span> Tarrick</div>
      <div class="contact__role">Owner</div>
      <ul class="contact__list">
        <li class="contact__item">
          <svg viewBox="0 0 24 24" aria-hidden="true"><path fill="var(--orange)" d="M6.6 10.8a15 15 0 0 0 6.6 6.6l2.2-2.2c.3-.3.7-.4 1-.2 1.1.4 2.3.6 3.6.6.6 0 1 .4 1 1V20c0 .6-.4 1-1 1A17 17 0 0 1 3 4c0-.6.4-1 1-1h3.5c.6 0 1 .4 1 1 0 1.3.2 2.5.6 3.6.1.3 0 .7-.2 1z"/><path fill="none" stroke="var(--orange)" stroke-width="2" d="M14 2.5a7.5 7.5 0 0 1 7.5 7.5M14 6a4 4 0 0 1 4 4"/></svg>
          614-502-7738
        </li>
        <li class="contact__item">
          <svg viewBox="0 0 24 24" aria-hidden="true"><circle cx="12" cy="12" r="10" fill="var(--orange)"/><path fill="var(--card)" d="M7 6c2 1 3 3 2 5s-3 2-3 4c-1-1-2-3-2-5 1-2 2-3 3-4zm7 3c2 0 4 2 3 4s-3 1-3 4c-1 1-2 2-3 2 0-2 1-3 0-5s1-5 3-5z"/></svg>
          www.skylarkreelworks.example
        </li>
      </ul>
    </div>

    <div class="credentials">
      NRD Certified Remote Pilot<br>Fully Insured
    </div>
  </section>
</body>
</html>
```